Book Cover for Lantern Cousins Notes from the Orchard

We have written a book that brings together Notes from the Orchard from a variety of women's voices.
We developed a draft book cover that we like using Canva (attached below). We'd love a book cover that is similar to this image, but looks more professional.
Following are the themes we’d like to depict in the book cover, and in parentheses, how they are represented in the current cover:
1. Divinely feminine (overall cover)
2. Currents of enlightenment (the swirls of light carrying the butterfly)
3. Diversity (a myriad of colors)
4. The solo journey into the unknown (the single butterfly’s flight)
5. Buoyancy and joy (again, the dancing colors and floating butterfly)
6. Boldly feminine (the blue butterfly, set against brush strokes of light)
7. Homage to a dear friend (she loved blue butterflies, the cosmos - this butterfly has hints of the cosmos in her wings, and painting - this background has brush strokes of light).
Book Title, Subtitle, and Editor:
Lantern Cousins
Notes from the Orchard
Edited by Ilse Varno
Thank you very much for considering this project!
People who are interested in Women and Spirituality

```html
<!DOCTYPE html>
<html lang="en">
<head>
<meta charset="utf-8">
<title>Lantern Cousins — Notes from the Orchard</title>
<link href="https://fonts.googleapis.com/css2?family=Oswald:wght@200&family=Mrs+Saint+Delafield&family=Montserrat:wght@500&display=swap" rel="stylesheet">
<style>
  :root {
    --backdrop: #a9b0b6;
    --cover-light: #fbf7bf;
    --cover-deep: #f5efa4;
    --title-blue: #3fb6e8;
    --ink: #1d1d1d;
    --band-pink: #ec79a3;
    --band-text: #ffffff;
    --wing-light: #39b4ec;
    --wing-deep: #1d3fae;
  }
  html, body {
    margin: 0;
    padding: 0;
    width: 1200px;
    height: 1200px;
    overflow: hidden;
    background: var(--backdrop);
  }
  .cover {
    position: absolute;
    left: 230px;
    top: 40px;
    width: 740px;
    height: 1120px;
    background: linear-gradient(180deg, var(--cover-light) 0%, var(--cover-deep) 100%);
    overflow: hidden;
  }
  .cover__title {
    position: absolute;
    left: 0;
    right: 0;
    top: 48px;
    margin: 0;
    text-align: center;
    font-family: "Oswald", sans-serif;
    font-weight: 200;
    font-size: 196px;
    line-height: 200px;
    letter-spacing: 2px;
    color: var(--title-blue);
    text-transform: uppercase;
  }
  .cover__title span { display: block; }
  .cover__subtitle {
    position: absolute;
    left: 0;
    right: 0;
    top: 555px;
    margin: 0;
    text-align: center;
    font-family: "Mrs Saint Delafield", cursive;
    font-weight: 400;
    font-size: 56px;
    color: var(--ink);
  }
  .cover__art {
    position: absolute;
    left: 265px;
    top: 680px;
    width: 285px;
    height: 280px;
    border-radius: 50% 40% 45% 55%;
    background: radial-gradient(circle at 55% 45%, var(--wing-light) 0%, var(--wing-deep) 80%);
  }
  .cover__band {
    position: absolute;
    left: 0;
    right: 0;
    bottom: 0;
    height: 108px;
    background: var(--band-pink);
    display: flex;
    align-items: center;
    justify-content: center;
  }
  .cover__editor {
    margin: 0;
    font-family: "Montserrat", sans-serif;
    font-weight: 500;
    font-size: 34px;
    letter-spacing: 3px;
    color: var(--band-text);
    text-transform: uppercase;
  }
</style>
</head>
<body>
  <main class="cover">
    <h1 class="cover__title"><span>Lantern</span><span>Cousins</span></h1>
    <p class="cover__subtitle">Notes from the Orchard</p>
    <div class="cover__art" role="img" aria-label="Illustration of a single glowing blue butterfly with starry wings"></div>
    <footer class="cover__band">
      <p class="cover__editor">Edited by Ilse Varno</p>
    </footer>
  </main>
</body>
</html>
```